Bright Pelvicare Business Card

Need a business card for a surgical practice called Bright Pelvicare. We have recently selected a logo (attached). The business card will need to have two formats:
1) One with the logo/physician name/ contact info on the front and location information on the back.
2) One in "appointment reminder card" style with the logo/ contact info/ date/ time on the front and the location information on the back.

The front side should include the following information:
- Logo
- Rohan K. Desai, MD FACOG
- phone: 469-555-0182
- fax: 1-469-555-0317
- email: admin@brightpelvi.com
- website: www.brightpelvicare.com

The back side should have the office locations listed:
4518 Kestrel Ave, Plano, TX 75198
3920 Bramwell Rd, Plano, TX 75147
2245 Silverpine Ln, Irving, TX 75163
815 W Garnet Ave S310, Dallas, TX 75284
3614 Lantern Blvd, Grand Prairie, TX 75179
7405 Amberly Crest Dr, San Antonio, TX 78391
5812 Tolliver Rd, Pasadena, TX 77639

Target Market(s)

1. Other physicians who might refer patients
2. Female patients

Industry/Entity Type

Business

Font styles to use
Other font styles liked:
• Tahoma for lettering

Requirements
Must have
• As per the instructions
Should not have
• No other images needed -- please try to keep font consistent with logo design. Can use Tahoma as the font for lettering.

```html
<!DOCTYPE html>
<html lang="en">
<head>
<meta charset="utf-8">
<title>Bright Pelvicare Stationery</title>
<link href="https://fonts.googleapis.com/css2?family=Lato:wght@400;700&display=swap" rel="stylesheet">
<style>
:root{
  --stage:#2a2a2a;
  --brand-blue:#0d63b3;
  --deep-blue:#1d4690;
  --light-blue:#3f86c9;
  --accent-red:#e0262b;
  --paper:#ffffff;
  --ink:#4a4a4a;
  --ghost:#dde4f1;
}
*{margin:0;padding:0;box-sizing:border-box}
html,body{width:1200px;height:711px;overflow:hidden;background:var(--stage);font-family:"Lato",Tahoma,sans-serif}
.canvas{position:relative;width:1200px;height:711px}

/* Folder */
.folder{position:absolute;left:59px;top:69px;width:411px;height:580px;background:var(--brand-blue);overflow:hidden}
.folder .brand{position:absolute;top:118px;left:0;width:100%;text-align:center;color:#fff;font-size:20px;font-weight:700;letter-spacing:.3px}
.folder .brand-dot{display:inline-block;width:12px;height:12px;border-radius:50%;background:#fff;margin-right:8px;vertical-align:1px}
.folder .emblem{position:absolute;left:20px;top:214px;width:371px;height:330px;border-radius:45% 45% 30% 30%;background:radial-gradient(ellipse at center,#3a7cc4 0%,#2f73bd 60%,var(--brand-blue) 100%)}
.folder .web{position:absolute;bottom:18px;width:100%;text-align:center;color:#fff;font-size:11px}

/* Letterhead */
.letter{position:absolute;left:483px;top:69px;width:411px;height:580px;background:var(--paper);overflow:hidden;color:var(--ink)}
.letter .brand{position:absolute;left:39px;top:52px;color:var(--brand-blue);font-size:11px;font-weight:700}
.brand-square{display:inline-block;width:8px;height:8px;background:var(--brand-blue);margin-right:5px}
.contact-list{position:absolute;right:26px;top:36px;list-style:none;font-size:7.5px;text-align:right;line-height:10px;color:#333}
.contact-list li svg{width:8px;height:7px;margin-left:4px;vertical-align:-1px}
.letter .side{position:absolute;left:21px;top:143px;width:80px;font-size:6.8px;line-height:9px}
.side .label{color:var(--brand-blue);font-weight:700;margin-top:18px}
.side .date{margin-bottom:0}
.letter .body{position:absolute;left:111px;top:143px;width:273px;font-size:6.5px;line-height:9.3px;text-align:justify}
.body .salutation{font-size:8.5px;margin-bottom:10px}
.body p{margin-bottom:9px}
.body .closing{margin-top:28px}
.signature{display:block;width:68px;height:9px;margin-top:3px;background:linear-gradient(90deg,#c9c9c9,#e6e6e6)}
.letter .footer-band{position:absolute;left:0;bottom:3px;width:100%;height:13px;background:var(--brand-blue)}
.footer-band .web{position:absolute;left:291px;top:0;width:94px;height:13px;background:var(--accent-red);color:#fff;font-size:7.5px;line-height:13px;text-align:center;border-left:2px solid #fff;border-right:2px solid #fff}

/* Cards */
.card{position:absolute;left:915px;width:238px;height:135px;border-radius:10px;overflow:hidden}
.card-front{top:346px;background:var(--paper)}
.card-front .brand{position:absolute;left:123px;top:41px;color:var(--brand-blue);font-size:9px;font-weight:700}
.card-front .name-band{position:absolute;left:0;top:37px;width:120px;height:12px;background:var(--deep-blue);color:#fff;font-size:7.5px;font-weight:700;line-height:12px;padding-left:18px}
.name-band small{font-size:5px;font-weight:400}
.card-front .rule{position:absolute;left:120px;top:50px;width:118px;height:1px;background:var(--brand-blue)}
.card-front .ghost{position:absolute;left:150px;top:58px;width:70px;height:66px;border-radius:45% 45% 35% 35%;background:var(--ghost)}
.card-front .card-contacts{position:absolute;left:17px;top:76px;list-style:none;font-size:5.5px;line-height:9px;color:#333}
.card-contacts svg{width:6px;height:5px;margin-right:4px;vertical-align:-.5px}
.card-front .footer-band{position:absolute;left:0;bottom:0;width:100%;height:9px;background:var(--brand-blue)}
.card-front .footer-band .web{position:absolute;left:14px;top:0;width:69px;height:9px;background:var(--accent-red);color:#fff;font-size:5px;line-height:9px;text-align:center}

.card-back{top:513px;background:linear-gradient(135deg,var(--deep-blue) 0%,#2d5fb0 50%,#234f9d 100%);color:#fff}
.card-back .ghost{position:absolute;left:110px;top:0;width:110px;height:120px;border-radius:45% 45% 35% 35%;background:radial-gradient(ellipse,rgba(255,255,255,.14),rgba(255,255,255,0) 70%)}
.card-back .web{position:absolute;right:16px;top:13px;font-size:5.5px}
.card-back h2{position:absolute;left:17px;top:44px;font-size:7.5px;font-weight:700}
.card-back ul{position:absolute;left:18px;top:60px;font-size:5.2px;line-height:9.4px;list-style:none}
.card-back li::before{content:"•";margin-right:4px}
</style>
</head>
<body>
<main class="canvas">

  <section class="folder">
    <div class="brand"><span class="brand-dot"></span>Bright Pelvicare</div>
    <div class="emblem" role="img" aria-label="Large faint brand emblem decoration"></div>
    <div class="web">www.brightpelvicare.com</div>
  </section>

  <section class="letter">
    <div class="brand"><span class="brand-square"></span>Bright Pelvicare</div>
    <ul class="contact-list">
      <li>469-555-0182<svg viewBox="0 0 8 7"><rect x="0" y="2" width="8" height="5" rx="1" fill="#0d63b3"/><rect x="1" y="0" width="6" height="2" fill="#0d63b3"/></svg></li>
      <li>1-469-555-0317<svg viewBox="0 0 8 7"><rect x="0" y="2" width="8" height="4" fill="#0d63b3"/><rect x="2" y="0" width="4" height="2" fill="#0d63b3"/><rect x="2" y="5" width="4" height="2" fill="#0d63b3"/></svg></li>
      <li>admin@brightpelvi.com<svg viewBox="0 0 8 7"><rect x="0" y="1" width="8" height="6" fill="#0d63b3"/><path d="M0 1 L4 4.5 L8 1" stroke="#fff" stroke-width=".8" fill="none"/></svg></li>
    </ul>
    <div class="side">
      <p class="date">13 October 2014</p>
      <p class="label">Address :</p>
      <p>123 Street Name, NY<br>Country</p>
      <p class="label">Daniel Harwick</p>
      <p>General Manager</p>
    </div>
    <div class="body">
      <p class="salutation">Dear Doe,</p>
      <p>Lorem ipsum dolor sit amet, consectetuer adipiscing elit, sed diam nonummy nibh euismod tincidunt ut laoreet dolore magna aliquam erat volutpat. Ut wisi enim ad minim veniam, quis nostrud exerci tation ullamcorper suscipit lobortis nisl ut aliquip ex ea commodo consequat. Duis autem vel eum iriure dolor in hendrerit in vulputate velit esse molestie consequat, vel illum dolore eu feugiat nulla facilisis at vero eros et accumsan et iusto odio dignissim qui blandit praesent luptatum zzril delenit augue duis dolore te feugait nulla facilisi. Nam liber tempor cum soluta nobis eleifend option congue nihil imperdiet doming id quod mazim placerat facer possim assum. Typi non habent claritatem insitam; est usus legentis in iis qui facit eorum claritatem. Investigationes demonstraverunt lectores legere me lius quod ii legunt saepius. Claritas est etiam processus dynamicus, qui sequitur mutationem consuetudium lectorum. Mirum est notare quam littera gothica, quam nunc putamus parum claram, anteposuerit litterarum formas humanitatis per seacula quarta decima et quinta decima. Eodem modo typi, qui nunc nobis videntur parum clari, fiant sollemnes in futurum.</p>
      <p>Lorem ipsum dolor sit amet, consectetuer adipiscing elit, sed diam nonummy nibh euismod tincidunt ut laoreet dolore magna aliquam erat volutpat. Ut wisi enim ad minim veniam, quis nostrud exerci tation ullamcorper suscipit lobortis nisl ut aliquip ex ea commodo consequat. Duis autem vel eum iriure dolor in hendrerit in vulputate velit esse molestie consequat, vel illum dolore eu feugiat nulla facilisis at vero eros et accumsan et iusto odio dignissim qui blandit praesent luptatum zzril delenit augue duis dolore te feugait nulla facilisi. Nam liber tempor cum soluta nobis eleifend option congue nihil imperdiet doming id quod mazim placerat facer possim assum. Typi non habent claritatem insitam; est usus legentis in iis qui facit eorum claritatem. Investigationes demonstraverunt lectores legere me lius quod ii legunt saepius. Claritas est etiam processus dynamicus, qui sequitur mutationem consuetudium lectorum. Mirum est notare quam littera gothica, quam nunc putamus parum claram, anteposuerit litterarum formas humanitatis per seacula quarta decima et quinta decima. Eodem modo typi, qui nunc nobis videntur parum clari, fiant sollemnes in futurum.</p>
      <p class="closing">Sincerely,</p>
      <span class="signature" role="img" aria-label="Handwritten signature"></span>
    </div>
    <div class="footer-band"><span class="web">www.brightpelvicare.com</span></div>
  </section>

  <section class="card card-front">
    <div class="name-band">Rohan K. Desai <small>- MD FACOG</small></div>
    <div class="rule"></div>
    <div class="brand">Bright Pelvicare</div>
    <div class="ghost" role="img" aria-label="Faint brand emblem decoration"></div>
    <ul class="card-contacts">
      <li><svg viewBox="0 0 8 7"><rect x="0" y="2" width="8" height="5" rx="1" fill="#0d63b3"/><rect x="1" y="0" width="6" height="2" fill="#0d63b3"/></svg>469-555-0182</li>
      <li><svg viewBox="0 0 8 7"><rect x="0" y="2" width="8" height="4" fill="#0d63b3"/><rect x="2" y="0" width="4" height="2" fill="#0d63b3"/></svg>1-469-555-0317</li>
      <li><svg viewBox="0 0 8 7"><rect x="0" y="1" width="8" height="6" fill="#0d63b3"/><path d="M0 1 L4 4.5 L8 1" stroke="#fff" stroke-width=".8" fill="none"/></svg>admin@brightpelvi.com</li>
    </ul>
    <div class="footer-band"><span class="web">www.brightpelvicare.com</span></div>
  </section>

  <section class="card card-back">
    <div class="ghost" role="img" aria-label="Faint brand emblem decoration"></div>
    <div class="web">www.brightpelvicare.com</div>
    <h2>Office Locations :</h2>
    <ul>
      <li>4518 Kestrel Ave, Plano, TX 75198</li>
      <li>3920 Bramwell Rd, Plano, TX 75147</li>
      <li>2245 Silverpine Ln, Irving, TX 75163</li>
      <li>815 W Garnet Ave S310, Dallas, TX 75284</li>
      <li>3614 Lantern Blvd, Grand Prairie, TX 75179</li>
      <li>7405 Amberly Crest Dr, San Antonio, TX 78391</li>
      <li>5812 Tolliver Rd, Pasadena, TX 77639</li>
    </ul>
  </section>

</main>
</body>
</html>
```